FREE BBQ for life if you win our business with your creative menu design

Looking for a 11x17 size menu. we are a full service BBQ restaurant. We have an upscale environment as well as up scale service. We offer 5 star dinning at a casual price. we are on route 84 and are proud of that. we offer the finest smoked meats. Specializing in smoked pork beef and bison. we have an old barn wood decor. we only use oak to smoke our meats. use a lot of tarnished metal as well as some string nail art. Looking for a menu that goes along our style. i have attached as many pictures as i could to give you a fill of how we do it out here.
PLEASE USE THE 11"X17" MENU TEMPLATE ATTACHED IN THE PROJECT BRIEF.
Target Market(s)
Cool people and there families.
Industry/Entity Type
Business
Requirements
Must have
- I have attached the Current menu we use. File brantlys menu pub. Those are all the Items. There will be some changes as we but together the new menu. The prices are changing. but that should be an easy change as we go.
Nice to have
- We are getting away from the lunch dinner menu and going to an all day menu. so rather than coming with toast or bun we will now be asking as an option. I have attached a menu i tried to make as a sample of how we will be doing it. new menu single page and new menu single page flame. These are ideas i had but could not really make it work. so use them as an idea of what we are looking for but be creative.

```html
<!DOCTYPE html>
<html lang="en">
<head>
<meta charset="utf-8">
<title>Fresh From the Grill – Menu</title>
<link rel="stylesheet" href="https://fonts.googleapis.com/css2?family=Bebas+Neue&family=Oswald:wght@500;600&family=Crimson+Text:ital,wght@0,400;0,600;1,400&family=Rye&family=Alfa+Slab+One&display=swap">
<style>
:root{
  --wood-dark:#2a3a3c;
  --wood-teal:#4d6f72;
  --wood-brown:#4a3a2c;
  --panel:rgba(14,16,18,.62);
  --text:#f2efe8;
  --accent:#e8742c;
  --flame-hi:#ffe59a;
  --flame-mid:#f59a2a;
  --flame-low:#b8321a;
  --rust:#6e4a32;
  --metal:#8c8a84;
}
*{margin:0;padding:0;box-sizing:border-box}
html,body{width:927px;height:1200px;overflow:hidden;background:#222}
.menu{position:relative;width:927px;height:1200px;overflow:hidden;
  background:
    repeating-linear-gradient(180deg,rgba(0,0,0,.28) 0 2px,transparent 2px 46px),
    linear-gradient(100deg,var(--wood-dark),var(--wood-teal) 35%,var(--wood-brown) 60%,var(--wood-teal) 85%,var(--wood-dark));
  font-family:"Crimson Text",Georgia,serif;color:var(--text)}
.base-strip{position:absolute;left:0;right:0;bottom:0;height:36px;background:linear-gradient(180deg,#5a4a3a,#7a7872)}
.decor{position:absolute}
.panel{position:absolute;left:56px;top:212px;width:808px;height:948px;background:var(--panel);border-radius:14px}
.title{position:absolute;left:320px;top:38px;width:440px;text-align:center}
.title-top{font-family:"Alfa Slab One",serif;font-size:31px;letter-spacing:1px;color:var(--flame-low);line-height:1}
.title-main{font-family:"Rye",serif;font-size:96px;line-height:.95;letter-spacing:4px;
  background:linear-gradient(180deg,var(--flame-hi),var(--flame-mid) 55%,var(--flame-low));
  -webkit-background-clip:text;background-clip:text;color:transparent}
.block{position:absolute}
.heading{font-family:"Bebas Neue","Oswald",sans-serif;font-weight:400;font-size:50px;line-height:.9;letter-spacing:.5px;color:#fff;margin-bottom:12px;white-space:nowrap}
.note{font-style:italic;font-size:9.6px;line-height:1.4;margin-bottom:10px}
.subhead{font-style:italic;font-weight:600;font-size:11px;margin-top:-6px}
.item{margin-bottom:9px;font-size:8.6px;line-height:1.5}
.item-name{display:block;color:var(--accent);font-weight:600;font-size:9.2px}
.list{font-size:8.6px;line-height:1.5}
.brands{display:flex;align-items:center;gap:16px;margin:8px 0 10px}
.brand{display:flex;align-items:center;gap:5px;font-size:16px;font-weight:600;color:#fff}
.brand-dot{width:22px;height:22px;border-radius:50%;background:#fff}
.kids-badge{position:absolute;left:86px;top:1022px;width:96px;height:88px}
.kids-badge p{position:absolute;left:0;right:0;text-align:center;font-family:"Oswald",sans-serif;color:#fff}
.loyalty{position:absolute;left:200px;top:1006px;width:124px;text-align:center}
.loyalty-circle{width:92px;height:92px;margin:0 auto;border-radius:50%;background:#fff;border:4px solid #3a6ea5;display:flex;align-items:center;justify-content:center;font-size:24px;font-weight:600;color:#3a6ea5}
.loyalty-band{margin-top:-10px;background:#1f4f86;font-family:"Oswald",sans-serif;font-size:8.4px;padding:3px 2px;color:#fff}
.loyalty-tag{width:92px;margin:2px auto 0;background:var(--accent);font-size:6.4px;line-height:1.2;padding:2px;color:#fff}
</style>
</head>
<body>
<main class="menu">
  <div class="decor" style="left:0;top:0;width:300px;height:230px;background:radial-gradient(ellipse at 45% 45%,#9a958a,#5e5a52 70%,transparent 72%)" role="img" aria-label="Tarnished metal wall decoration"></div>
  <svg class="decor" style="left:790px;top:0" width="137" height="60" role="img" aria-label="Rusted metal disc">
    <ellipse cx="70" cy="5" rx="64" ry="40" fill="var(--rust)"/>
  </svg>
  <svg class="decor" style="left:745px;top:215px" width="182" height="390" role="img" aria-label="String and nail art sign in blue and orange">
    <rect x="10" y="15" width="172" height="360" rx="6" fill="#3d6f92" transform="rotate(-8 90 200)"/>
  </svg>
  <svg class="decor" style="left:0;top:290px" width="70" height="330" role="img" aria-label="Tarnished highway shield sign">
    <ellipse cx="10" cy="165" rx="58" ry="160" fill="#6a5470"/>
  </svg>
  <svg class="decor" style="left:0;top:680px" width="44" height="180" role="img" aria-label="Rusted metal disc">
    <ellipse cx="0" cy="90" rx="42" ry="88" fill="var(--rust)"/>
  </svg>
  <svg class="decor" style="left:740px;top:655px" width="187" height="460" role="img" aria-label="Rusted route sign and weathered plank art">
    <rect x="30" y="0" width="157" height="460" rx="10" fill="#4a3a48"/>
  </svg>

  <div class="panel"></div>

  <header class="title">
    <div class="title-top">FRESH FROM THE</div>
    <div class="title-main">GRILL</div>
  </header>

  <section class="block" style="left:86px;top:240px;width:225px">
    <h2 class="heading">APPETIZER</h2>
    <div class="item"><span class="item-name">King Rings</span>Green Chili battered fried golden crispy 1" thick onion rings. 7.89</div>
    <div class="item"><span class="item-name">Deep Fried Pickles</span>Crisp dill pickle chips battered and fried to a golden crispy brown. 7.89</div>
    <div class="item"><span class="item-name">Fried Okra</span>Okra is breaded then fried until golden. 7.89</div>
    <div class="item"><span class="item-name">Green Chili Waffle Fries</span>Crispy waffle-cut Fries, topped with a savory blend of cheese, and New Mexico green chile. 7.89</div>
    <div class="item"><span class="item-name">KC Wild Wings</span>Big, meaty pork wings, deep fried to a perfect golden brown, tossed in a hot and tangy Buffalo-style sauce, and served with spicy buttermilk ranch dressing on the side. 9.99</div>
    <div class="item"><span class="item-name">Sampler Platter</span>Two KC Wild Wings, 6oz Fried Pickles, 3 King Rings. 8.99</div>
  </section>

  <section class="block" style="left:86px;top:604px;width:250px">
    <h2 class="heading">BISON</h2>
    <p class="subhead">Heart Healthy</p>
    <p class="note">Comes with 1 side dish and your choice of Texas toast, Kaiser bun, Whole wheat bread or Glutton Free bread</p>
    <div class="item"><span class="item-name">Bison Burger</span>Smoked then grilled served with pepper jack cheese lettuce tomato pickle toped with spicy ranch. 12.59</div>
    <div class="item"><span class="item-name">Bison Brisket</span>The belly of beast, smoked then sliced thin and grilled. Juicy and tender 18.65</div>
    <div class="item"><span class="item-name">Bison Steak</span>12oz of lean healthy meat cooked to your desired temp. 34.56</div>
  </section>

  <section class="block" style="left:86px;top:852px;width:240px">
    <h2 class="heading">SIDE DISHES</h2>
    <div class="list">Green Chile Creamed Corn<br>Potato Salad<br>Baked Potato<br>Grilled Veggies<br>Baked Beans<br>Waffle Fries<br>Extra side 2.29</div>
  </section>

  <div class="kids-badge">
    <svg width="96" height="88"><polygon points="48,2 92,24 92,64 48,86 4,64 4,24" fill="#2f8fd0"/></svg>
    <p style="top:18px;font-size:9px">KIDS UNDER 4</p>
    <p style="top:32px;font-size:12px">EAT FREE!</p>
    <p style="top:50px;font-size:10px">SEE Kids menu</p>
  </div>

  <div class="loyalty">
    <div class="loyalty-circle">Tallyo</div>
    <div class="loyalty-band">JOIN OUR CUSTOMER LOYALTY APP</div>
    <div class="loyalty-tag">Get FREE FOOD when you become a loyal customer.</div>
  </div>

  <section class="block" style="left:355px;top:240px;width:460px">
    <h2 class="heading">SMOKED</h2>
    <p class="note">Comes with 1 side dish and your choice of Texas toast, Kaiser bun, Whole wheat bread or Glutton Free bread</p>
  </section>
  <section class="block" style="left:356px;top:316px;width:205px">
    <div class="item"><span class="item-name">Baby Back Ribs</span>Tender to the bone, finger licking good, never need a knife, best ribs you'll ever have.<br>Full Rack 19.96 &nbsp;&nbsp; Half Rack 11.49</div>
    <div class="item"><span class="item-name">St. Louis Ribs</span>A nice big tender spare rib, slow smoked to tender that you can sink your teeth into.<br>Full Rack 30.98 &nbsp;&nbsp; Half Rack 16.45</div>
    <div class="item"><span class="item-name">Beef Brisket</span>The most insane mouth watering smoky, moist, succulent piece of meat your mouth will ever have. 10.95</div>
    <div class="item"><span class="item-name">Pulled Pork</span>Smoked for 18-20 hrs. then pulled and mixed with our signature base barbeque sauce. 9.59</div>
  </section>
  <section class="block" style="left:612px;top:316px;width:208px">
    <div class="item"><span class="item-name">Sliced Pork</span>Smoked juicy tenderloin sliced thin then grilled per order. 9.54</div>
    <div class="item"><span class="item-name">Smoked Turkey</span>Breast meat smoked and sliced. Juicy and tender. 9.49</div>
    <div class="item"><span class="item-name">Smoked Chicken Half</span>Moist and juicy smoked Breast and thigh on the bone basted with our signature sauce on the grill. 13.59</div>
    <div class="item"><span class="item-name">Smoked Sausage</span>Made in house and slow smoked. Your choice of spicy or not. Add to any meal 5.99 &nbsp; As a meal 11.89</div>
    <div class="item"><span class="item-name">Rib Eye</span>12oz juicy steak grilled to your desired temp. 21.95</div>
  </section>

  <section class="block" style="left:355px;top:574px;width:215px">
    <h2 class="heading">DESSERTS</h2>
    <div class="item"><span class="item-name">Peach Cobbler &amp; Ice Cream</span>Served hot topped with ice cream<br>Small 3.89 &nbsp;&nbsp; Large 5.89</div>
    <div class="item"><span class="item-name">Cookies A-L-Mode</span>2 hot gooey cookies topped with ice cream your choice chocolate chip or macadamia nut<br>Small 3.89 &nbsp;&nbsp; Large 5.89</div>
    <div class="item"><span class="item-name">Dessert of the week</span>Ask your server for our special dessert of the week</div>
  </section>

  <section class="block" style="left:354px;top:780px;width:215px">
    <h2 class="heading">SALADS</h2>
    <div class="item"><span class="item-name">All You Can Eat Salad &nbsp;<span style="color:var(--text);font-weight:400">7.89</span></span>Side Salad 3.00 &nbsp;&nbsp; With Meal 1.50</div>
    <div class="item"><span class="item-name">Add Meat To Your Salad</span>Choose from any sliced meat. 3.00</div>
  </section>

  <section class="block" style="left:353px;top:906px;width:215px">
    <h2 class="heading">DRINKS</h2>
    <div class="item"><span class="item-name">Lemonade</span>Regular, Strawberry, Watermelon Cherry, Peach 2.59</div>
    <div class="item" style="margin-bottom:0"><span class="item-name">Fountain</span></div>
    <div class="brands">
      <span class="brand"><span class="brand-dot"></span>Fizzo</span>
      <span class="brand"><span class="brand-dot"></span>Doc Spice</span>
    </div>
    <div class="item">Fizzo, Doc Spice, Root Beer, Sierra Breeze, Mtn Surge, Diet Fizzo Diet Doc Spice 1.89</div>
    <div class="item"><span class="item-name">Iced Teas</span>Sweetened, Unsweetened 1.89</div>
  </section>

  <section class="block" style="left:612px;top:556px;width:208px">
    <h2 class="heading">BB CUSTOMS</h2>
    <div class="item"><span class="item-name">BBQ Tacos</span>Three Tacos in blue and red shells with your choice of meat topped with shredded lettuce and Pico-D-BBQ and Spicy ranch.<br>(Excludes ribs and bison.) 9.89</div>
    <div class="item"><span class="item-name" style="display:inline">Taco Tuesday</span> is a Must! 5.00 tacos all day</div>
    <div class="item"><span class="item-name">Rowdy Chicken Sandwich</span>Skinless boneless chicken breasts breaded fried, topped with pepper jack cheese, lettuce, tomato onion and pickles. On a buttery grilled Texas toast. 10.59</div>
    <div class="item"><span class="item-name">Pick Two Specials</span>Pick any 2 (two) meats from Smoked section. 15.99</div>
    <div class="item"><span class="item-name">Create Your Own Wrap</span>Pick your own meat, cheese, the additionals and sauce.</div>
    <div class="item"><span class="item-name">The Potato</span>Baked potato loaded with cheese, your choice of meat, green chile, topped with lettuce, pico-D-bbq and spicy ranch sauce. 9.49</div>
  </section>

  <section class="block" style="left:612px;top:944px;width:200px">
    <h2 class="heading">EXTRAS</h2>
    <div class="list">With Green Chile &nbsp;&nbsp; 1.50<br>Cheese &nbsp;&nbsp; 1.50<br>Bacon &nbsp;&nbsp; 1.50<br>Extra meat &nbsp;&nbsp; 3.00<br>Extra sauce &nbsp;&nbsp; 0.50<br>Grilled onions &nbsp;&nbsp; Free of Charge</div>
  </section>

  <div class="base-strip"></div>
</main>
</body>
</html>
```